its a new company based in Christchurch new Zealand building computers ,repairs, upgrades and anything computers for the general public,i like bright happy colours like yellows, greens reds anything that stands out and it needs to communicant trust and security towards my new company,i have no logo yet,

Target Market(s)

target market of all ages

Industry/Entity Type

Building

Contact Information for Business Card

Byte Harbour Limited,ph-0218847261,email-tidelark77@mailvesta.test,14c marlowe cres,fenwick

```html
<!DOCTYPE html>
<html lang="en">
<head>
<meta charset="utf-8">
<title>Byte Harbour – Business Card</title>
<link rel="stylesheet" href="https://fonts.googleapis.com/css2?family=Russo+One&family=Exo+2:wght@500;600&family=Great+Vibes&display=swap">
<style>
  :root {
    --backdrop: #e8e8ea;
    --card-deep: #5e0f2e;
    --card-mid: #a3173f;
    --card-bright: #d8284c;
    --card-peach: #f08a72;
    --ink-light: #ffffff;
    --ink-soft: rgba(255, 255, 255, 0.85);
    --rule: rgba(255, 255, 255, 0.45);
    --badge-fill: #f4f1ec;
    --badge-ink: #4a4a4a;
    --mark-gold: #e0b23a;
    --screen-blue: #2a7fc4;
    --case-dark: #1c1c20;
  }
  * { box-sizing: border-box; margin: 0; padding: 0; }
  html, body {
    width: 1200px; height: 801px; overflow: hidden;
    background: var(--backdrop);
  }
  .canvas {
    position: relative; width: 1200px; height: 801px;
  }
  .card {
    position: absolute; left: 120px; top: 120px;
    width: 960px; height: 561px; overflow: hidden;
    border-radius: 4px;
    background:
      radial-gradient(ellipse 70% 55% at 40% 105%, var(--card-peach) 0%, rgba(240,138,114,0) 70%),
      linear-gradient(125deg, var(--card-deep) 0%, var(--card-mid) 40%, var(--card-bright) 75%, #e2445a 100%);
    box-shadow: 0 18px 40px rgba(0,0,0,0.18);
    font-family: "Exo 2", sans-serif;
    color: var(--ink-light);
  }
  .brand-top {
    position: absolute; left: 500px; top: 36px;
    font-family: "Russo One", sans-serif; font-size: 46px;
    letter-spacing: 1px; text-transform: uppercase;
  }
  .brand-main {
    position: absolute; left: 48px; top: 160px;
    display: flex; align-items: center; gap: 18px;
  }
  .brand-dot {
    width: 62px; height: 62px; border-radius: 50%;
    background: var(--mark-gold);
  }
  .brand-name {
    font-family: "Russo One", sans-serif; font-size: 40px;
    text-transform: uppercase; letter-spacing: 1px;
  }
  .hero-art {
    position: absolute; left: 70px; top: 250px;
    width: 330px; height: 170px; border-radius: 6px;
    background: linear-gradient(135deg, var(--case-dark) 0%, var(--screen-blue) 55%, #0f3f6e 100%);
  }
  .divider {
    position: absolute; left: 470px; top: 110px;
    width: 1px; height: 290px; background: var(--rule);
  }
  .services {
    position: absolute; left: 500px; top: 112px;
    list-style: none; font-size: 23px; font-weight: 600;
  }
  .services li {
    display: flex; align-items: center; gap: 12px; height: 32px;
  }
  .services svg { width: 20px; height: 20px; flex: none; }
  .guarantee {
    position: absolute; left: 505px; top: 228px;
    width: 270px; height: 84px; border-radius: 42px;
    background: var(--badge-fill); border: 3px solid #cfc9c0;
    color: var(--badge-ink); text-align: center;
  }
  .guarantee-script {
    display: block; font-family: "Great Vibes", cursive;
    font-size: 24px; margin-top: 6px;
  }
  .guarantee-word {
    display: block; font-family: "Russo One", sans-serif;
    font-size: 28px; letter-spacing: 2px; line-height: 1;
  }
  .contact {
    position: absolute; right: 40px; top: 350px;
    text-align: right; font-size: 24px; font-weight: 500;
    line-height: 1.35; color: var(--ink-soft);
  }
  .address {
    position: absolute; left: 70px; top: 450px;
    font-size: 25px; font-weight: 500; line-height: 1.35;
  }
</style>
</head>
<body>
<main class="canvas">
  <section class="card">
    <h1 class="brand-top">Byte Harbour</h1>

    <div class="brand-main">
      <span class="brand-dot"></span>
      <span class="brand-name">Byte Harbour</span>
    </div>

    <div class="hero-art" role="img" aria-label="Desktop computer with tower, monitor, keyboard and mouse"></div>

    <span class="divider"></span>

    <ul class="services">
      <li><svg viewBox="0 0 20 20" fill="none" stroke="#fff" stroke-width="2.4" stroke-linecap="round"><path d="M6 5.5a7 7 0 1 0 8 0"/><path d="M10 2v7"/></svg>Building Computers</li>
      <li><svg viewBox="0 0 20 20" fill="none" stroke="#fff" stroke-width="2.4" stroke-linecap="round"><path d="M6 5.5a7 7 0 1 0 8 0"/><path d="M10 2v7"/></svg>Computer Repairs</li>
      <li><svg viewBox="0 0 20 20" fill="none" stroke="#fff" stroke-width="2.4" stroke-linecap="round"><path d="M6 5.5a7 7 0 1 0 8 0"/><path d="M10 2v7"/></svg>Computer Upgrades</li>
    </ul>

    <div class="guarantee">
      <span class="guarantee-script">100% Satisfaction</span>
      <span class="guarantee-word">GUARANTEED</span>
    </div>

    <address class="contact">
      tidelark77@mailvesta.test<br>
      021 884 7261
    </address>

    <address class="address">
      Byte Harbour Limited<br>
      14c Marlowe Cres, Fenwick
    </address>
  </section>
</main>
</body>
</html>
```